Wealth Education Business Needs Sharp Business Card Design

We need a business card design for a recently launched investor education business called Harbor Crest.

The final design should promote security, empowerment, self improvement and financial gain. The card will ideally promote the stature of the business.

For more information and colours please visit harborcrest.com.au

Target Market(s)

Corporate executives and high net worth individuals

Industry/Entity Type

Education

Contact Information for Business Card

```html
<!DOCTYPE html>
<html lang="en">
<head>
<meta charset="utf-8">
<title>Harbor Crest – Business Card</title>
<link href="https://fonts.googleapis.com/css2?family=Exo+2:wght@400;500;600&display=swap" rel="stylesheet">
<style>
  :root {
    --backdrop: #e4e6e8;
    --card-top: #ffffff;
    --card-bottom: #e9eaeb;
    --charcoal: #3d3b3c;
    --teal: #0f6f6e;
    --teal-faint: rgba(15, 111, 110, 0.14);
    --accent-blue: #1e9ad6;
    --ink: #3a3a3a;
    --ink-soft: #4a4a4a;
  }
  * { margin: 0; padding: 0; box-sizing: border-box; }
  html, body {
    width: 1200px; height: 900px; overflow: hidden;
    background: var(--backdrop);
    font-family: "Exo 2", sans-serif;
  }
  .business-card {
    position: absolute; left: 110px; top: 170px;
    width: 980px; height: 560px;
    border-radius: 44px; overflow: hidden;
    box-shadow: 0 18px 40px rgba(0,0,0,0.18);
  }
  .card-background { position: absolute; inset: 0; }
  .brand-mark {
    position: absolute; left: 150px; top: 160px;
    width: 80px; height: 80px; border-radius: 50%;
    background: var(--teal);
  }
  .brand-watermark {
    position: absolute; left: 450px; top: 160px;
    width: 220px; height: 220px; border-radius: 50%;
    background: var(--teal-faint);
  }
  .holder {
    position: absolute; right: 70px; top: 58px; text-align: right;
  }
  .holder-name {
    color: var(--accent-blue); font-size: 27px; font-weight: 500;
    letter-spacing: 2px;
  }
  .holder-title {
    color: var(--ink); font-size: 18px; font-weight: 500; letter-spacing: 1.5px;
  }
  .contact-list {
    position: absolute; right: 56px; top: 150px; list-style: none;
    text-align: right; color: var(--ink-soft); font-size: 17px; letter-spacing: 0.8px;
  }
  .contact-list li {
    display: flex; justify-content: flex-end; align-items: center;
    gap: 10px; height: 27px;
  }
  .contact-list svg { width: 18px; height: 18px; fill: var(--accent-blue); }
  .brand-name {
    position: absolute; left: 62px; top: 262px;
    color: var(--ink); font-size: 46px; font-weight: 500; letter-spacing: 6px;
  }
  .office-address {
    position: absolute; left: 70px; top: 340px;
    color: var(--ink); font-size: 22px; font-weight: 500; line-height: 34px;
    letter-spacing: 1px; font-style: normal;
  }
</style>
</head>
<body>
  <div class="business-card">
    <svg class="card-background" viewBox="0 0 980 560" preserveAspectRatio="none" aria-hidden="true">
      <defs>
        <linearGradient id="card-surface" x1="0" y1="0" x2="0" y2="1">
          <stop offset="0" stop-color="var(--card-top)"/>
          <stop offset="1" stop-color="var(--card-bottom)"/>
        </linearGradient>
      </defs>
      <rect width="980" height="560" fill="url(#card-surface)"/>
      <path class="teal-swoosh" fill="var(--teal)"
        d="M240,446 C540,432 780,380 980,312 L980,356 C720,420 500,442 240,446 Z"/>
      <path class="charcoal-band" fill="var(--charcoal)"
        d="M0,466 C340,464 660,428 980,368 L980,560 L0,560 Z"/>
    </svg>

    <div class="brand-watermark" role="img" aria-label="Faint brand emblem decoration"></div>
    <div class="brand-mark" role="img" aria-label="Brand emblem"></div>

    <div class="holder">
      <div class="holder-name">JORDAN AVERY</div>
      <div class="holder-title">PRESIDENT</div>
    </div>

    <ul class="contact-list">
      <li>020 481 7362
        <svg viewBox="0 0 24 24"><path d="M6.6 10.8a15 15 0 0 0 6.6 6.6l2.2-2.2a1 1 0 0 1 1-.25 11.4 11.4 0 0 0 3.6.57 1 1 0 0 1 1 1V20a1 1 0 0 1-1 1A17 17 0 0 1 3 4a1 1 0 0 1 1-1h3.5a1 1 0 0 1 1 1c0 1.25.2 2.45.57 3.6a1 1 0 0 1-.25 1z"/></svg>
      </li>
      <li>020 481 7363
        <svg viewBox="0 0 24 24"><path d="M7 1h10a2 2 0 0 1 2 2v18a2 2 0 0 1-2 2H7a2 2 0 0 1-2-2V3a2 2 0 0 1 2-2zm0 3v14h10V4zm5 15.5a1.2 1.2 0 1 0 0 2.4 1.2 1.2 0 0 0 0-2.4z"/></svg>
      </li>
      <li>020 481 7364
        <svg viewBox="0 0 24 24"><path d="M3 8h3v13H3zm5-5h9v6H8zm0 8h13v10H8zm3 2v2h2v-2zm4 0v2h2v-2zm-4 4v2h2v-2zm4 0v2h2v-2z"/></svg>
      </li>
      <li>info@harborcrest.com.au
        <svg viewBox="0 0 24 24"><path d="M2 5h20v14H2zm2 2v.5l8 5.5 8-5.5V7zm0 2.9V17h16V9.9l-8 5.5z"/></svg>
      </li>
      <li>www.harborcrest.com.au
        <svg viewBox="0 0 24 24"><path d="M12 2a10 10 0 1 0 0 20 10 10 0 0 0 0-20zm6.9 6h-3a15 15 0 0 0-1.3-3.9A8 8 0 0 1 18.9 8zM12 4c.8 1.1 1.5 2.5 1.9 4h-3.8c.4-1.5 1.1-2.9 1.9-4zM4.3 14a8 8 0 0 1 0-4h3.4a16 16 0 0 0 0 4zm.8 2h3a15 15 0 0 0 1.3 3.9A8 8 0 0 1 5.1 16zm3-8h-3a8 8 0 0 1 4.3-3.9A15 15 0 0 0 8.1 8zM12 20c-.8-1.1-1.5-2.5-1.9-4h3.8c-.4 1.5-1.1 2.9-1.9 4zm2.3-6H9.7a14 14 0 0 1 0-4h4.6a14 14 0 0 1 0 4zm.3 5.9a15 15 0 0 0 1.3-3.9h3a8 8 0 0 1-4.3 3.9zM16.3 14a16 16 0 0 0 0-4h3.4a8 8 0 0 1 0 4z"/></svg>
      </li>
    </ul>

    <div class="brand-name">HARBOR CREST</div>

    <address class="office-address">
      041.12th floor,Quay<br>Harbour Road NSW
    </address>
  </div>
</body>
</html>
```